SaaS / Consulting / Solution website redesign

We need a website design that:
- Is completely different than our current design : https://plumvessel.net
- Has a very minimal amount of copy
- Changes our positioning from a SaaS application to a solutions company. Solutions company means that we help our customers solve their problems with consulting, training, and tools. An example of a solutions company is here: https://oldpages.example/web/20130111103320/http://www.brindlework.com:80/
- Does not make us look like a start up
- Is more people oriented than technology oriented

We need a designer that:
- Is a rebel at heart
- Is a minimalist
- Tells us why our current site sucks
- Can disagree with us
- Can also do copywriting or already has a copywriter that can help
- Is ok with saying we have capability that we don't in order to see if people actually want that
- Can understand the difference between our grand vision and where we need to focus ourselves today in order to get there

Who we are:
- Entrepreneurs
- Programmers
- Consultants
- Investors

Here's our design goals:
#1 Get customers, investors, employers, and partners excited about our unique and clearly articulated value proposition
#2 Get people to contact us asking for help with their programs
#3 Position ourselves as an expert in the skills based volunteering, mentorship, and group collaboration
#4 Make it easy for people, who already know who we are, to register online

What our grand vision is:
- Create a marketplace where any person can go to our site and find time with anyone they need to meet with. Whether that is their hair stylist, school advisor, parent of your kids class, dentist, attorney, etc.

What will you get if you win:
- In addition to the prize of this project we will have many landing pages and other revisions we will need in the future. We currently don't have a designer or copywriter and need to add that capability to our team

Who do we need to appeal to:
- Directors that are launching innovative programs inside organizations
- IT personnel who are trying to disqualify our technology so they don't have to support it or deal with it when it doesn't go well
- Enterprise IT architects who don't want our product being on its own island within their organization totally incompatible with everything else. Architects which are trying to assess how our platform will co-exist with all their other platforms
- Vice Presidents who want to help their directors understand that we don't have enough experience to help them
- Program managers who have to juggle a million things and need a tool that actually helps instead of confuses them and adds more work for them.
- Program managers & directors that have been given ambiguous goals by their board of directors like "improve retention, increase engagement, create innovation, get people to collaborate." And who have no idea where to start or how to deliver on things like that.
- Program managers, directors, and vice presidents that are trying to understand how our technology and services fit into their existing technology and capability
- Employees who are bored and uninspired with their current tools and are hoping for some excitement in their life. Kind of like candy or a double espresso.
- Investors who think, our company like all the rest, are going to waste their money and make them look like a fool

Other information:
-The CSS and html needs to be responsive

-Our registration onboarding flow needs to collect this information:
User first name
user last name
user email
(verify their email)
user phone number
(verify their phone number)
User profile image (optional)
User profile summary (optional, like a bio, freeform text fiels)
If applicable: Register their organization
Organization name
Organization image (optional)
Account Mailing address
account Billing address (could be same as mailing address)
account Billing email address (could be same as user address)
account Product selection (pricing tier)
account Credit card information

The designs I am getting are a good start but they are only the front page. I just want you to know that I am expecting and need more than a landing page to complete the design. I will likely need a page that outlines the benefits and features of the product itself, how its different than our competitors, which will not be on the front page. I will need a registration flow. I will need a blog page design so we can post blog articles, I will need a team page, a page that goes into detail on our training, our services. I will likely need a page that shows all news and media we have been in. I need to show customer and user quotes, case studies, a way to contact us, partners, general resources like on collaboration, product tutorials, customers. I need the site to address a comprehensive set of needs. I need that design to be consistent and thorough. I know what PlateHarbor is. I'm not using because I need more than a template that was customized. I need to be unique and match our brand thoughtfully, beautifully, and artistically. Someone asked me a question about how Murmly is similar to our tool in the way it is referred by end users and purchased by managers. Our website needs to primarily talk to the managers as I explained in the brief but it needs to appear cool and exciting to our end-users without focusing on the technology too much. Murmly is a tool that teams use to collaborate in small and large enterprises. The value prop for them is that communication is easier. But they don't put that on their website. Why? Because the users of the technology won't go to the website to find out information on it, they get their information from someone who is using it and demos it to them. When Ines tells her manager Otto "Lets get murmly, Ruth is using it at her company and its great" Ines's manager doesn't know anything about murmly so she promptly googles it. The most important thing from Ines's perspective is that Otto agrees to try it out. Otto's biggest concern is that productivity will be enhanced to degraded. Murmly knows this and so on the front page they know they are talking to Otto NOT Ines because Ines is already sold on it and doesn't need to get sold on the website. Ines is end user. Otto is the purchaser. We have the same problem and so our end users are not the ones purchasing our product, their managers are purchasing our product. We get referred by our end users and vetted by their managers. Hope this helps! Thank you for looking at this project!  Added Wednesday, June 7, 2017

Another observation I am having about the designs being submitted. I believe we used the animations on our current website because animations / cartoons connect with the "inner child" in our users. Whatever that means :-). I think it's what makes our brand fun. I have a hard time imagining that we could make the design fun looking without animations but I'm sure it can be achieved. I also recognize that blending pictures of real people and animations is hard. So either we must masterfully blend them, use only animations, or make the real people have a LOT of fun! So far most of the designs while achieve the goal of appealing to the serious Vice Presidents and directors, they are not doing a good job at appealing to the overworked program managers and bored employees. There seems to stand another challenge with animations which is animations are hard to find and/or create that achieve the message / emotion we are trying to communicate. I don't have any good answers for this but I will say we can hire both animators and illustrators if we need to. All you have to do is communicate the effect in the website design with some simpler version maybe not the end illustration or animation itself. Added Wednesday, June 7, 2017

• Sex appeal and a sense of humor. Copy that makes people excited and clairvoyant about our potential.
• Boring renditions of other non-inspiring websites

```html
<!DOCTYPE html>
<html lang="en">
<head>
<meta charset="utf-8">
<title>Plumvessel – Register Now</title>
<link href="https://fonts.googleapis.com/css2?family=Roboto:wght@300;400;500;700&family=Open+Sans:wght@400&display=swap" rel="stylesheet">
<style>
:root{
  --blue:#1aa3f0;
  --green:#7fc97a;
  --green-deep:#5cb455;
  --ink:#333;
  --body:#4a4a4a;
  --muted:#8a8a8a;
  --line:#d6d8dc;
  --footer:#f0f1f5;
  --icon:#7d8088;
}
*{box-sizing:border-box;margin:0;padding:0}
html,body{width:818px;height:1200px;overflow:hidden}
body{position:relative;font-family:'Roboto',sans-serif;color:var(--ink);background:#fff}
.abs{position:absolute}
.brand{display:flex;align-items:center;gap:6px;color:var(--blue);font-size:15px;font-weight:400}
.brand-dot{width:20px;height:20px;border-radius:50%;border:2px solid var(--green)}
.nav{left:325px;top:36px;font-size:6.5px;font-weight:500}
.nav a{position:absolute;white-space:nowrap;text-decoration:none;color:var(--muted)}
.nav a.current{color:var(--blue)}
.btn{display:flex;align-items:center;justify-content:center;text-decoration:none;white-space:nowrap}
.btn-login{left:593px;top:30px;width:47px;height:20px;background:var(--green);color:#fff;font-size:7px;font-weight:500;border:1px solid #6ab864}
.btn-register{left:644px;top:30px;width:66px;height:20px;background:var(--blue);color:#fff;font-size:7px;font-weight:500}
.register{left:0;top:70px;width:818px;height:431px;background:linear-gradient(180deg,#fff 0%,#f7f8fa 60%,#fafbfc 100%)}
.register h1{position:absolute;top:14px;width:818px;text-align:center;font-weight:300;font-size:26px;color:#222}
.field{position:absolute;left:234px;width:351px;height:27px;border:1px solid var(--line);background:#fff;font-size:7px;color:var(--body);padding:10px 11px}
.form-actions .btn{position:absolute;top:332px;width:118px;height:29px;font-size:9.5px;color:#fff;font-weight:400}
.btn-subscribe{left:288px;background:linear-gradient(#3c9be3,#2a7fcc)}
.btn-org{left:425px;background:var(--green)}
.team-band{left:0;top:501px;width:818px;height:221px;background:linear-gradient(100deg,#86cf7d 0%,#6cbf62 35%,#62b85a 55%,#80cc77 100%)}
.team-band h2{position:absolute;top:55px;width:818px;text-align:center;color:#fff;font-family:'Open Sans',sans-serif;font-weight:400;font-size:17px;line-height:25px;letter-spacing:.8px}
.band-btn{position:absolute;top:129px;width:129px;height:26px;font-size:8.5px;font-weight:400;letter-spacing:.3px}
.band-btn.demo{left:277px;background:#fff;color:var(--blue)}
.band-btn.brochure{left:412px;border:1px solid #fff;color:#fff}
.experience-title{left:0;top:758px;width:818px;text-align:center;font-size:15px;font-weight:400;letter-spacing:1px;color:#555}
.clients{left:120px;top:808px;width:580px;height:36px;display:flex;justify-content:space-between;align-items:center}
.client{font-size:9px;font-weight:700;color:#2b4a7a;text-align:center;line-height:1.1}
.divider{left:110px;top:859px;width:599px;height:1px;background:#e3e4e6}
.col{top:877px;width:200px}
.col-head{display:flex;align-items:center;gap:6px;font-size:9.5px}
.col-icon{width:21px;height:21px;border-radius:50%}
.col p{font-size:7px;line-height:12.3px;color:var(--body);margin-top:5px}
.col .more{font-size:6.5px;color:var(--blue);margin-top:4px}
.vsep{top:868px;width:1px;height:108px;background:#e3e4e6}
.footer{left:0;top:993px;width:818px;height:207px;background:var(--footer)}
.footer-text{left:110px;top:1070px;width:310px;font-size:7px;line-height:12px;color:var(--body)}
.f-btn{top:1114px;height:18px;font-size:6.5px;font-weight:500;letter-spacing:.3px}
.f-btn.demo{left:116px;width:69px;background:var(--blue);color:#fff}
.f-btn.brochure{left:190px;width:94px;background:#fff;color:var(--blue)}
.f-links a{position:absolute;top:1072px;font-size:6.5px;color:#555;text-decoration:none}
.f-email{left:518px;top:1116px;width:130px;height:16px;border-bottom:1px solid #d8d9dd;font-size:6px;color:#d0d2d6;padding-top:3px}
.f-sub{left:654px;top:1115px;width:54px;height:18px;background:#fff;color:var(--blue);font-size:6.5px;font-weight:500}
.f-rule{left:110px;top:1158px;width:599px;height:1px;background:#dadbe0}
.copy{top:1174px;font-size:6.5px;color:var(--body)}
.social{top:1167px;width:9px;height:9px}
</style>
</head>
<body>

<header>
  <div class="abs brand" style="left:110px;top:28px"><span class="brand-dot"></span>Plumvessel</div>
  <nav class="abs nav">
    <a class="current" style="left:0">Home</a>
    <a style="left:43px">Product</a>
    <a style="left:93px">About</a>
    <a style="left:137px">Library</a>
    <a style="left:185px">Careers</a>
    <a style="left:235px">Contact</a>
  </nav>
  <a class="abs btn btn-login">Login</a>
  <a class="abs btn btn-register">Register Now</a>
</header>

<section class="abs register">
  <h1>Register Now</h1>
  <div class="field" style="top:76px">First Name</div>
  <div class="field" style="top:112px">Last Name</div>
  <div class="field" style="top:148px">Email</div>
  <div class="field" style="top:184px">Phone</div>
  <div class="field" style="top:220px">Profile Image (Optional)</div>
  <div class="field" style="top:256px;height:58px">Profile Summary (Optional)</div>
  <div class="form-actions">
    <a class="btn btn-subscribe">SUBSCRIBE</a>
    <a class="btn btn-org">REGISTER ORGANIZATON</a>
  </div>
</section>

<section class="abs team-band" role="img" aria-label="Photo of a laughing, high-fiving team working together around a table, tinted green">
  <h2>Because it takes the perfect team<br>to bring great innovations to life</h2>
  <a class="btn band-btn demo">REQUEST DEMO</a>
  <a class="btn band-btn brochure">DOWNLOAD BROCHURE</a>
</section>

<h3 class="abs experience-title">OUR EXPERIENCE</h3>
<div class="abs clients">
  <span class="client" style="font-size:11px">Harborline</span>
  <span class="client" style="color:#3a8a3a">Quillstone</span>
  <span class="client">Merrow Health</span>
  <span class="client" style="font-size:11px">Tallis<br>Systems</span>
  <span class="client" style="font-size:11px">Brantwood</span>
  <span class="client" style="color:#8a1a1a">Coastmark</span>
  <span class="client" style="font-weight:400">Skyreach<br>Air</span>
  <span class="client" style="color:#111">Dunmore<br>Energy</span>
</div>
<div class="abs divider"></div>

<article class="abs col" style="left:108px">
  <div class="col-head" style="color:var(--blue)"><span class="col-icon" style="background:var(--blue)"></span>Latest News</div>
  <p>07-06-2017<br>Lorem Ipsum is simply dummy text of the printing and typesetting industry. Lorem Ipsum has been the industry's standard dummy text ever since the 1500s</p>
  <div class="more">Read More</div>
</article>
<div class="abs vsep" style="left:311px"></div>
<article class="abs col" style="left:341px">
  <div class="col-head" style="color:var(--green-deep)"><span class="col-icon" style="background:var(--green-deep)"></span>Tutorials</div>
  <p>- Lorem Ipsum is simply dummy text of the<br>- Printing and typesetting industry.<br>- Lorem Ipsum has been the industry's standard<br>- Dummy text ever since the 1500s</p>
</article>
<div class="abs vsep" style="left:510px"></div>
<article class="abs col" style="left:542px;width:170px">
  <div class="col-head"><span class="col-icon" style="background:var(--icon)"></span>Case Studies:</div>
  <p>Case 1<br>Lorem Ipsum is simply dummy text of the printing and typesetting industry. Lorem Ipsum has been the industry's standard dummy text ever since the 1500s</p>
  <div class="more">Read More</div>
</article>

<footer class="abs footer"></footer>
<div class="abs brand" style="left:110px;top:1040px;font-size:16px"><span class="brand-dot"></span>Plumvessel</div>
<p class="abs footer-text">Lorem Ipsum is simply dummy text of the printing and typesetting industry. Lorem Ipsum has been the industry's standard dummy text ever since the 1500s</p>
<a class="abs btn f-btn demo">REQUEST DEMO</a>
<a class="abs btn f-btn brochure">DOWNLOAD BROCHURE</a>
<div class="f-links">
  <a style="left:522px">CONTACT</a>
  <a style="left:598px">ABOUT</a>
  <a style="left:660px">IMPRESSUM</a>
</div>
<div class="abs f-email">YOUREMAIL.COM</div>
<a class="abs btn f-sub">SUBSCRIBE</a>
<div class="abs f-rule"></div>
<p class="abs copy" style="left:110px">© 2017 Plumvessel Inc All rights reserved | Plumvessel® is a registered trademark of Plumvessel Inc</p>
<p class="abs copy" style="left:442px">Blog</p>
<p class="abs copy" style="left:478px">Press</p>

<svg class="abs social" style="left:643px" viewBox="0 0 10 10" aria-label="Share" role="img">
  <g fill="var(--icon)"><circle cx="2" cy="5" r="1.6"/><circle cx="8" cy="2" r="1.6"/><circle cx="8" cy="8" r="1.6"/></g>
  <path d="M2 5 8 2M2 5 8 8" stroke="var(--icon)" stroke-width="1"/>
</svg>
<svg class="abs social" style="left:671px" viewBox="0 0 10 10" aria-label="Message" role="img">
  <path d="M1 1.5h8v5.5H4L2 9V7H1z" fill="var(--icon)"/>
</svg>
<svg class="abs social" style="left:699px" viewBox="0 0 10 10" aria-label="Video" role="img">
  <path d="M3 1.5 8.5 5 3 8.5z" fill="var(--icon)"/>
</svg>

</body>
</html>
```